Business Intelligence Application - Reporting Menu and Report Criteria Design

Looking for a fresh, effective and user friendly view for the menu structure and reporting criteria screen format for a business reporting application. Initial format completed, content structure is in place, but we need the 'wow' design.. as its a serious professional report/BI tool it has to fall within certain guidelines for clarity and graphics..but we want it to be slick, friendly, great user experience. There is a large amount of complex content to fit into a small space and we need it to be very inviting, modern and intuitive.. If interested, please review the attachment. We have live screens in operation, but feel these could be improved and looking forward to seeing what great creative suggestions could be made. Please review work done to date in the attached.. We are not looking for a total re-design of everything, all the basic business content/structure is there.. but tell us what we could do to improve this in terms of graphic design... particularly the criteria screens.. thanks!
Updates

Reason: Need a few more days to review designs - thanks for all submissions so far, we will make a selection shortly.

Target Market(s)

Business analysts, hotel operations teams, finance analysts hospitality industry

Industry/Entity Type

Hospitality

Coding

Coded - Design and coding required

Number of Pages Required

4 page

Font styles to use
Sans Serif
Other font styles liked:
• Candara, please see example in deck

Colors
3276b5
3176b5
0255a3
85acd3
33a6d7
cee9f5
85cae6

Requirements
Must have
• sharp clear, logical menu structure, (currently it has 'clicks to sub-menus, we need hover over, slide to sub-menus..) colour, styling.. and most focus on revision of criteria.. right now is somewhat heavy, cumbersome.. keep colour and friendly intuitive process steps.. its heavy analytical stuff.. best of luck!
Should not have
• No grey fonts on white or grey screens! many business apps are not readable or sharp.. or fonts are too small.. colourless, so please avoid that.. see our deck - sharp dark (navy) or black fonts on white, or light shading..

```html
<!DOCTYPE html>
<html lang="en">
<head>
<meta charset="utf-8">
<title>Yieldscope – Property Search</title>
<link rel="stylesheet" href="https://fonts.googleapis.com/css2?family=Mulish:wght@400;600;700&display=swap">
<style>
  :root {
    --navy: #011633;
    --nav-blue: #0255a3;
    --nav-active: #4aaedd;
    --body-top: #33a6d7;
    --body-bottom: #0a5eae;
    --panel: #54b6e0;
    --white: #ffffff;
    --field-top: #ffffff;
    --field-bottom: #e9e9e9;
    --field-border: #c9d4dc;
    --field-text: #4a4f55;
    --list-hover: #e2e2e2;
    --accent: #33a6d7;
    --button: #0255a3;
    --footer: #e0e0e0;
    --footer-text: #6a6a6a;
    --divider: #1b2f4d;
  }
  * { box-sizing: border-box; margin: 0; padding: 0; }
  html, body { width: 1200px; height: 664px; overflow: hidden; }
  body {
    font-family: "Mulish", "Candara", sans-serif;
    position: relative;
    background: var(--footer);
  }

  /* Top bar */
  .top-bar {
    position: absolute; left: 0; top: 0; width: 1200px; height: 113px;
    background: var(--navy);
  }
  .brand {
    position: absolute; left: 97px; top: 42px;
    display: flex; align-items: center; gap: 14px;
  }
  .brand-mark { width: 30px; height: 30px; border-radius: 50%; background: var(--accent); }
  .brand-name { color: var(--white); font-size: 27px; font-weight: 700; letter-spacing: .2px; }
  .user-avatar {
    position: absolute; left: 781px; top: 34px; width: 44px; height: 44px;
    border-radius: 50%; background: radial-gradient(circle at 50% 40%, #c9b8a6, #6e7380);
  }
  .user-greeting {
    position: absolute; left: 833px; top: 36px; color: var(--white);
    font-size: 14px; line-height: 21px;
  }
  .user-greeting strong { font-weight: 600; display: block; }
  .top-divider { position: absolute; top: 40px; width: 1px; height: 38px; background: var(--divider); }
  .top-icon { position: absolute; top: 44px; }

  /* Main navigation */
  .main-nav {
    position: absolute; left: 0; top: 113px; width: 1200px; height: 51px;
    background: var(--nav-blue); display: flex; padding-left: 97px;
  }
  .nav-item {
    display: flex; align-items: center; gap: 8px; padding: 0 16px 0 11px;
    color: var(--white); font-size: 18px; font-weight: 600;
    border-right: 1px solid rgba(255,255,255,.35); height: 100%;
  }
  .nav-item:first-child { padding-left: 11px; margin-left: -11px; }
  .nav-item:last-child { border-right: none; }
  .nav-item.is-active { background: var(--nav-active); padding: 0 20px 0 44px; }
  .nav-item svg { width: 20px; height: 20px; fill: var(--white); }

  /* Content area */
  .content {
    position: absolute; left: 0; top: 164px; width: 1200px; height: 424px;
    background: linear-gradient(180deg, var(--body-top), var(--body-bottom));
  }
  .search-panel {
    position: absolute; left: 112px; top: 19px; width: 974px; height: 320px;
    background: var(--panel);
  }
  .field-label {
    position: absolute; color: var(--white); font-size: 17.5px; font-weight: 600;
  }
  .field-label.is-plain { font-weight: 400; }
  .field {
    position: absolute; width: 282px; height: 43px;
    background: linear-gradient(180deg, var(--field-top), var(--field-bottom));
    border: 1px solid var(--field-border);
    color: var(--field-text); font-size: 15.5px;
    display: flex; align-items: center; padding-left: 17px;
  }
  .field .chevron { position: absolute; right: 16px; top: 15px; }
  .search-button {
    position: absolute; left: 708px; top: 233px; width: 215px; height: 51px;
    background: var(--button); color: var(--white);
    font-size: 19.5px; font-weight: 700; letter-spacing: .3px;
    display: flex; align-items: center; justify-content: center; border-radius: 2px;
  }

  /* Open dropdowns */
  .option-list { position: absolute; width: 282px; box-shadow: 0 1px 3px rgba(0,0,0,.15); }
  .option {
    height: 43px; display: flex; align-items: center; padding-left: 20px;
    font-size: 15.5px; color: var(--field-text);
    background: linear-gradient(180deg, var(--field-top), var(--field-bottom));
    border: 1px solid var(--field-border); border-top: none;
  }
  .option.is-hover { background: var(--list-hover); }
  .option.is-selected { background: var(--nav-active); color: var(--white); }

  /* Footer */
  .footer-note {
    position: absolute; left: 0; top: 613px; width: 1200px; text-align: center;
    color: var(--footer-text); font-size: 13px;
  }
  .page-code { position: absolute; left: 1162px; top: 630px; color: var(--footer-text); font-size: 12.5px; }
</style>
</head>
<body>

<header class="top-bar">
  <div class="brand">
    <span class="brand-mark"></span>
    <span class="brand-name">Yieldscope</span>
  </div>
  <div class="user-avatar" role="img" aria-label="Profile photo of the signed-in administrator"></div>
  <div class="user-greeting">Welcome<strong>Admin</strong></div>
  <span class="top-divider" style="left:919px"></span>
  <svg class="top-icon" style="left:946px" width="28" height="28" viewBox="0 0 24 24" aria-label="Notifications">
    <path fill="#2a7fc0" d="M12 22a2.5 2.5 0 0 0 2.5-2.5h-5A2.5 2.5 0 0 0 12 22zm7-6V11a7 7 0 0 0-5.5-6.8V3.5a1.5 1.5 0 0 0-3 0v.7A7 7 0 0 0 5 11v5l-2 2v1h18v-1z"/>
  </svg>
  <span class="top-divider" style="left:1005px"></span>
  <svg class="top-icon" style="left:1035px" width="28" height="26" viewBox="0 0 24 22" aria-label="Sign out">
    <path fill="#2a7fc0" d="M14 2l9 8-9 8v-5C8 13 4 15 1 20c1-7 5-12 13-13z"/>
  </svg>
</header>

<nav class="main-nav">
  <div class="nav-item">
    <svg viewBox="0 0 24 24"><circle cx="12" cy="7" r="5"/><path d="M2 23c0-6 4-9 10-9s10 3 10 9z"/></svg>Admin
  </div>
  <div class="nav-item" style="padding-left:30px">
    <svg viewBox="0 0 24 24"><rect x="9" y="1" width="6" height="6"/><rect x="1" y="17" width="6" height="6"/><rect x="9" y="17" width="6" height="6"/><rect x="17" y="17" width="6" height="6"/><path d="M11 7h2v4h8v6h-2v-4h-6v4h-2v-4H5v4H3v-6h8z"/></svg>Management
  </div>
  <div class="nav-item is-active">
    <svg viewBox="0 0 24 24"><circle cx="10" cy="10" r="7" fill="none" stroke="#fff" stroke-width="3"/><path d="M15 15l7 7" stroke="#fff" stroke-width="3.5" stroke-linecap="round"/></svg>Property Search
  </div>
  <div class="nav-item" style="padding-left:36px;padding-right:32px">
    <svg viewBox="0 0 24 24"><circle cx="12" cy="12" r="11"/><path fill="#0255a3" d="M6 6c2 0 3 2 5 2s1 3-1 3-3 2-2 4-2 2-3 0-1-6 1-9zm9 8c2-1 4 0 4 2s-2 3-3 2-3-3-1-4zm0-10c2 0 4 1 5 3-2 0-3-1-5-3z"/></svg>Intel
  </div>
  <div class="nav-item" style="padding-left:24px">
    <svg viewBox="0 0 24 24"><path d="M10 1h4l.6 3 2.2 1 2.6-1.7 2.8 2.8L20.5 8.7l1 2.3 2.5.5v4l-2.5.5-1 2.3 1.7 2.6-2.8 2.8-2.6-1.7-2.2 1L14 26h-4l-.6-3-2.2-1-2.6 1.7-2.8-2.8 1.7-2.6-1-2.3L0 15.5v-4l2.5-.5 1-2.3-1.7-2.6 2.8-2.8L7.2 5l2.2-1z" transform="scale(.92) translate(1 -1)"/><circle cx="12" cy="12" r="3.5" fill="#0255a3"/></svg>Planning
  </div>
</nav>

<main class="content">
  <section class="search-panel">
    <label class="field-label" style="left:45px;top:45px">SEARCH NAME</label>
    <label class="field-label" style="left:344px;top:45px">SEARCH ID</label>
    <label class="field-label" style="left:639px;top:45px">SEARCH PRODUCT</label>
    <div class="field" style="left:45px;top:74px">Coral Bay Hotel</div>
    <div class="field" style="left:344px;top:74px"></div>
    <div class="field" style="left:639px;top:74px"></div>

    <label class="field-label" style="left:45px;top:146px">DIVISIONS</label>
    <label class="field-label" style="left:344px;top:146px">REGIONS</label>
    <label class="field-label is-plain" style="left:639px;top:146px">Areas</label>
    <div class="field" style="left:45px;top:176px">North Amercia
      <svg class="chevron" width="24" height="13" viewBox="0 0 24 13"><path d="M1 1l11 10L23 1" fill="none" stroke="#8a8f94" stroke-width="2"/></svg>
    </div>
    <div class="field" style="left:344px;top:176px">Select
      <svg class="chevron" width="24" height="13" viewBox="0 0 24 13"><path d="M1 1l11 10L23 1" fill="none" stroke="#8a8f94" stroke-width="2"/></svg>
    </div>
    <div class="field" style="left:639px;top:176px">
      <svg class="chevron" width="24" height="13" viewBox="0 0 24 13"><path d="M1 1l11 10L23 1" fill="none" stroke="#8a8f94" stroke-width="2"/></svg>
    </div>

    <div class="search-button">SEARCH</div>

    <div class="option-list" style="left:45px;top:219px">
      <div class="option">Southwest USA</div>
      <div class="option is-hover">Northwest USA</div>
    </div>
    <div class="option-list" style="left:328px;top:257px;border-top:1px solid var(--field-border)">
      <div class="option" style="padding-left:28px">Coral Bay Hotel</div>
      <div class="option is-selected" style="padding-left:28px">Harbor View Hotel</div>
    </div>
  </section>
</main>

<footer>
  <p class="footer-note">© 2017 Company Name&nbsp; All right reserved&nbsp; Term of Use</p>
  <span class="page-code">X14</span>
</footer>

</body>
</html>
```